Talon Microsystems PowerPoint Master Slide Deck Design

This is a 2-phase project to design a slide deck for a semiconductor company in the Silicon Valley. The design budget will be increased with each phase.
The slide deck will need to have one version with a dark background for presentations and a second version with a white background. Otherwise, the slides will be the same. I anticipate we will need a total of 10 slides, but that number may change.
The first phase will be to design a Title and a Title and Content slide.
- The Title Slide is the first slide of the deck. It should include the presentation title, the presenter's name and date of presentation
- The Title and Content slide should include a title and content with bullet points and up to 2 additional sub-bullets
- The Title and Content slide should have a footer that includes the slide #, Talon Microsystems Confidential, and the logo. This footer will be on every slide except the Title Slide
The first two slides will serve as the format for the remaining ~8 slides:
-Header and Content Text (1, 2, 4 column)
-Header and Content Image (bar chart, pie chart, tables)
-Break
-Title only
-Closing (Talon logo only)
Our slides contain a lot of content so a clean and simple design is best.
Both phases will need to include pre-set color options for
-Text and Lines
-Shadows
-Bullets and sub-bullets (including shapes, ex. circle, slash, square, etc.)
-Bar charts, pie charts, tables
Samples of our collateral are attached. Logo files are also attached
Look and feel
Each slider illustrates characteristics of the customer's brand and the style your logo design should communicate.

```html
<!DOCTYPE html>
<html lang="en">
<head>
<meta charset="utf-8">
<title>Talon Microsystems Slide Deck</title>
<link href="https://fonts.googleapis.com/css2?family=Roboto:wght@400;500;700;900&display=swap" rel="stylesheet">
<style>
:root{
  --ink:#000000;
  --blue:#0b57b5;
  --blue-dark:#0a4a9c;
  --blue-bright:#1d63d6;
  --pale:#c9dcef;
  --teal:#14a890;
  --white:#ffffff;
  --muted:#d8d8d8;
}
*{margin:0;padding:0;box-sizing:border-box}
html,body{width:1200px;height:4065px;overflow:hidden;background:#fff;font-family:'Roboto',Arial,sans-serif;color:var(--white)}
.slide{position:absolute;left:76px;width:1030px;height:580px;background:var(--ink);overflow:hidden}
.s1{top:73px}.s2{top:728px}.s3{top:1381px}.s4{top:2036px}.s5{top:2691px}.s6{top:3345px}
.edge-top{position:absolute;left:0;top:0;width:100%;height:5px;background:var(--blue)}
.edge-bottom{position:absolute;left:0;bottom:0;width:100%;height:5px;background:var(--blue)}
.photo{position:absolute}
.brand{display:flex;align-items:center;justify-content:center;gap:10px;font-weight:700;color:var(--white)}
.brand .dot{border-radius:50%;border:3px solid var(--blue-bright)}
/* title slide */
.s1 .photo{inset:0;background:radial-gradient(ellipse at 60% 35%,#3a3128 0%,#1a1c22 40%,#0c1016 75%)}
.s1 .brand{position:absolute;top:130px;left:0;right:0;font-size:34px}
.s1 .brand .dot{width:36px;height:36px}
.deck-title{position:absolute;top:238px;left:0;right:0;text-align:center;font-size:40px;font-weight:700;line-height:1.2}
.deck-sub{position:absolute;top:362px;left:0;right:0;text-align:center;font-size:13px}
.presenter{position:absolute;top:392px;left:0;right:0;text-align:center;font-size:15px;font-weight:500}
.date-pill{position:absolute;top:425px;left:460px;width:112px;height:26px;border-radius:13px;background:var(--teal);font-size:10px;display:flex;align-items:center;justify-content:center;gap:6px}
/* footer */
.footer{position:absolute;left:0;bottom:0;width:100%;height:53px;background:var(--blue);display:flex;align-items:center}
.footer .conf{position:absolute;left:43px;font-size:12px;font-weight:500;letter-spacing:.2px}
.footer .brand{position:absolute;left:0;right:0;font-size:14px}
.footer .brand .dot{width:16px;height:16px;border-width:2px;border-color:var(--white)}
.footer .page{position:absolute;right:0;top:0;width:147px;height:53px;background:var(--blue-bright);display:flex;align-items:center;justify-content:center;font-size:12px;font-weight:700}
.heading{position:absolute;font-size:25px;font-weight:700;color:var(--blue-bright);text-transform:uppercase}
.heading::after{content:"";display:block;width:66px;height:3px;background:var(--blue-bright);margin-top:4px}
/* about */
.s2 .heading{left:43px;top:82px}
.col{position:absolute;top:140px;width:440px;font-size:11px;line-height:1.62}
.col.left{left:43px}.col.right{left:515px}
.col ul{list-style:none}
.col li{position:relative;padding-left:16px;margin-bottom:12px}
.col li::before{content:"";position:absolute;left:2px;top:5px;border-left:7px solid var(--muted);border-top:4px solid transparent;border-bottom:4px solid transparent}
.col ul ul{margin-top:10px}
.col ul ul li{margin-left:22px;margin-bottom:10px;font-size:10.5px}
.col > ul > li{margin-bottom:24px}
/* what we do */
.s3 .photo{left:0;top:0;width:100%;height:290px;background:linear-gradient(120deg,#2a2420 0%,#1b2028 45%,#34302a 70%,#15181d 100%)}
.s3 h2{position:absolute;top:108px;left:0;right:0;text-align:center;font-size:25px;font-weight:700}
.s3 h2::after{content:"";display:block;width:70px;height:3px;background:var(--white);margin:4px auto 0}
.s3 .lead{position:absolute;top:158px;left:300px;width:430px;text-align:center;font-size:14px;line-height:1.45}
.service{position:absolute;top:242px;width:260px;text-align:center}
.service .icon{width:96px;height:96px;margin:0 auto;border-radius:50%;background:var(--blue);border:3px solid var(--white);display:flex;align-items:center;justify-content:center}
.service p{margin-top:26px;font-size:11px;line-height:1.62}
/* semiconductor */
.s4 .quad{position:absolute;width:258px;height:263px}
.q-photo1{left:0;top:0;background:linear-gradient(135deg,#8fb4d8,#3a5f8c 55%,#d9e6f2)}
.q-text1{left:258px;top:0;background:var(--pale);color:#111;font-size:10.5px;line-height:1.95;padding:28px 34px}
.q-text2{left:0;top:263px;background:var(--pale);color:#111;font-size:10.5px;line-height:1.95;padding:28px 34px}
.q-photo2{left:258px;top:263px;background:linear-gradient(160deg,#5a2a3a,#1f3b6a 55%,#4a8fc0)}
.s4 .heading{left:557px;top:64px}
.s4 .body{position:absolute;left:563px;top:122px;width:420px;font-size:10.5px;line-height:1.95}
/* company */
.s5 .heading{left:43px;top:70px}
.s5 .body{position:absolute;left:43px;top:126px;width:455px;font-size:12.5px;line-height:1.72}
.orb{position:absolute;border-radius:50%;border:4px solid var(--teal)}
.orb1{left:740px;top:23px;width:242px;height:242px;background:radial-gradient(circle,#1f8a6e 0%,#123a34 45%,#2b211c 100%)}
.orb2{left:548px;top:278px;width:210px;height:210px;background:radial-gradient(circle at 50% 55%,#f0a24a 0%,#7a4b2a 35%,#2c3a4a 75%)}
/* closing */
.s6 .brand{position:absolute;top:255px;left:0;right:0;font-size:52px;color:var(--blue-bright);gap:18px}
.s6 .brand .dot{width:56px;height:56px;border-width:5px}
</style>
</head>
<body>

<section class="slide s1">
  <div class="photo" role="img" aria-label="Dark close-up photo of a circuit board with a processor chip"></div>
  <div class="edge-top"></div>
  <div class="brand"><span class="dot"></span>Talon Microsystems</div>
  <h1 class="deck-title">TALON<br>MICROSYSTEMS</h1>
  <p class="deck-sub">Lorem ipsum dolor sit amet, consectetur adipiscing elit</p>
  <p class="presenter">Dana Whitfield</p>
  <div class="date-pill">
    <svg width="10" height="10" viewBox="0 0 10 10"><rect x="1" y="2" width="8" height="7" fill="none" stroke="#fff"/><line x1="1" y1="4" x2="9" y2="4" stroke="#fff"/></svg>
    04/10/2023
  </div>
  <div class="edge-bottom"></div>
</section>

<section class="slide s2">
  <h2 class="heading">About Us</h2>
  <div class="col left">
    <ul>
      <li>Lorem ipsum dolor sit amet, consectetur adipiscing elit, sed do eiusmod tempor incididunt ut labore et dolore magna aliqua. Ut enim ad Lorem ipsum dolor sit amet, consectetur adipiscing elit, sed do eiusmod tempor incididunt ut labore
        <ul>
          <li>Lorem ipsum dolor sit amet, consectetur adipiscing elit, sed do eiusmod tempor incididunt ut labore et dolore magna aliqua. Ut enim ad minim veniam,</li>
          <li>Lorem ipsum dolor sit amet, consectetur adipiscing elit, sed do eiusmod tempor incididunt ut labore et dolore magna aliqua. Ut enim ad minim veniam,</li>
        </ul>
      </li>
      <li>Lorem ipsum dolor sit amet, consectetur adipiscing elit, sed do eiusmod tempor incididunt ut labore et dolore magna aliqua. Ut enim ad Lorem ipsum dolor sit amet, consectetur adipiscing elit, sed do eiusmod tempor incididunt ut labore
        <ul>
          <li>Lorem ipsum dolor sit amet, consectetur adipiscing elit, sed do eiusmod tempor incididunt ut labore et dolore magna aliqua. Ut enim ad minim veniam,</li>
          <li>Lorem ipsum dolor sit amet, consectetur adipiscing elit, sed do eiusmod tempor incididunt ut labore et dolore magna aliqua. Ut enim ad minim veniam,</li>
        </ul>
      </li>
    </ul>
  </div>
  <div class="col right">
    <ul>
      <li>Lorem ipsum dolor sit amet, consectetur adipiscing elit, sed do eiusmod tempor incididunt ut labore et dolore magna aliqua. Ut enim ad Lorem ipsum dolor sit amet, consectetur adipiscing elit, sed do eiusmod tempor incididunt ut labore
        <ul>
          <li>Lorem ipsum dolor sit amet, consectetur adipiscing elit, sed do eiusmod tempor incididunt ut labore et dolore magna aliqua. Ut enim ad minim veniam,</li>
          <li>Lorem ipsum dolor sit amet, consectetur adipiscing elit, sed do eiusmod tempor incididunt ut labore et dolore magna aliqua. Ut enim ad minim veniam,</li>
        </ul>
      </li>
      <li>Lorem ipsum dolor sit amet, consectetur adipiscing elit, sed do eiusmod tempor incididunt ut labore et dolore magna aliqua. Ut enim ad Lorem ipsum dolor sit amet, consectetur adipiscing elit, sed do eiusmod tempor incididunt ut labore
        <ul>
          <li>Lorem ipsum dolor sit amet, consectetur adipiscing elit, sed do eiusmod tempor incididunt ut labore et dolore magna aliqua. Ut enim ad minim veniam,</li>
          <li>Lorem ipsum dolor sit amet, consectetur adipiscing elit, sed do eiusmod tempor incididunt ut labore et dolore magna aliqua. Ut enim ad minim veniam,</li>
        </ul>
      </li>
    </ul>
  </div>
  <footer class="footer"><span class="conf">TALON MICROSYSTEMS CONFIDENTIAL</span><div class="brand"><span class="dot"></span>Talon Microsystems</div><span class="page">PAGE | 02</span></footer>
</section>

<section class="slide s3">
  <div class="photo" role="img" aria-label="Photo of a processor chip mounted on a circuit board"></div>
  <h2>WHAT WE DO</h2>
  <p class="lead">Lorem ipsum dolor sit amet, consectetur adipiscing elit, sed do eiusmod tempor incididunt ut labore et dolore magna aliqua.</p>
  <div class="service" style="left:35px">
    <div class="icon"><svg width="40" height="40" viewBox="0 0 40 40" fill="none" stroke="#fff" stroke-width="2"><rect x="10" y="10" width="20" height="20"/><rect x="15" y="15" width="10" height="10"/><path d="M14 4v6M20 4v6M26 4v6M14 30v6M20 30v6M26 30v6M4 14h6M4 20h6M4 26h6M30 14h6M30 20h6M30 26h6"/></svg></div>
    <p>Lorem ipsum dolor sit amet, consectetur adipiscing elit, sed do eiusmod tempor incididunt ut labore et dolore magna aliqua. Ut enim ad minim veniam, quis nostrud exercitation ullamco laboris nisi ut aliquip ex ea commodo consequat.</p>
  </div>
  <div class="service" style="left:384px">
    <div class="icon"><svg width="40" height="40" viewBox="0 0 40 40" fill="none" stroke="#fff" stroke-width="2"><rect x="11" y="6" width="18" height="28" rx="1"/><path d="M15 12h10M15 17h10M15 22h6"/></svg></div>
    <p>Lorem ipsum dolor sit amet, consectetur adipiscing elit, sed do eiusmod tempor incididunt ut labore et dolore magna aliqua. Ut enim ad minim veniam, quis nostrud exercitation ullamco laboris nisi ut aliquip ex ea commodo consequat.</p>
  </div>
  <div class="service" style="left:733px">
    <div class="icon"><svg width="40" height="40" viewBox="0 0 40 40" fill="none" stroke="#fff" stroke-width="2"><path d="M20 8l14 8-14 8-14-8z"/><path d="M6 22l14 8 14-8"/><path d="M16 16l4-2 4 2-4 2z"/></svg></div>
    <p>Lorem ipsum dolor sit amet, consectetur adipiscing elit, sed do eiusmod tempor incididunt ut labore et dolore magna aliqua. Ut enim ad minim veniam, quis nostrud exercitation ullamco laboris nisi ut aliquip ex ea commodo consequat.</p>
  </div>
  <footer class="footer"><span class="conf">TALON MICROSYSTEMS CONFIDENTIAL</span><div class="brand"><span class="dot"></span>Talon Microsystems</div><span class="page">PAGE | 03</span></footer>
</section>

<section class="slide s4">
  <div class="quad q-photo1" role="img" aria-label="Photo of a bright semiconductor fabrication lab"></div>
  <div class="quad q-text1">Lorem ipsum dolor sit amet, consectetur adipiscing elit, sed do eiusmod tempor incididunt ut labore et dolore magna aliqua. Ut enim ad minim veniam, quis nostrud exercitation ullamco laboris nisi ut aliquip ex ea commodo consequat.Lorem ipsum dolor sit amet, consectetur adipiscing elit, sed do eiusmod tempor incididunt ut labore et</div>
  <div class="quad q-text2">Lorem ipsum dolor sit amet, consectetur adipiscing elit, sed do eiusmod tempor incididunt ut labore et dolore magna aliqua. Ut enim ad minim veniam, quis nostrud exercitation ullamco laboris nisi ut aliquip ex ea commodo consequat.Lorem ipsum dolor sit amet, consectetur adipiscing elit, sed do eiusmod tempor incididunt ut labore et</div>
  <div class="quad q-photo2" role="img" aria-label="Photo of a machine probing a chip under red and blue light"></div>
  <h2 class="heading">Semiconductor</h2>
  <p class="body">Lorem ipsum dolor sit amet, consectetur adipiscing elit, sed do eiusmod tempor incididunt ut labore et dolore magna aliqua. Ut enim ad minim veniam, quis nostrud exercitation ullamco laboris nisi ut aliquip ex ea commodo consequat. Duis aute irure dolor in reprehenderit in voluptate velit esse cillum dolore eu fugiat nulla pariatur. Excepteur sint occaecat cupidatat non proident, sunt in culpa qui officia deserunt mollit anim id est laborum.Lorem ipsum dolor sit amet, consectetur adipiscing elit, sed do eiusmod tempor incididunt ut labore et dolore magna aliqua. Ut enim ad minim veniam, quis nostrud exercitation ullamco laboris nisi ut aliquip ex ea commodo consequat. Duis aute irure dolor in reprehenderit in voluptate velit esse cillum dolore eu fugiat nulla pariatur. Excepteur sint occaecat cupidatat non proident, sunt in culpa qui officia deserunt mollit anim id est laborum.Lorem ipsum dolor sit amet, consectetur adipiscing elit, sed do eiusmod tempor incididunt ut labore et dolore magna aliqua. Ut enim ad minim veniam, quis nostrud exercitation ullamco laboris nisi ut aliquip ex ea commodo consequat. Duis aute irure dolor in reprehenderit in voluptate velit esse cillum dolore eu fugiat nulla pariatur. Excepteur sint occaecat cupidatat non proident, sunt in culpa qui officia deserunt mollit anim id est laborum.Lorem ipsum dolor sit amet, consectetur adipiscing elit, sed do eiusmod tempor incididunt ut labore et dolore magna aliqua. Ut enim ad minim veniam, quis nostrud exercitation ullamco laboris nisi</p>
  <footer class="footer"><span class="conf">TALON MICROSYSTEMS CONFIDENTIAL</span><div class="brand"><span class="dot"></span>Talon Microsystems</div><span class="page">PAGE | 04</span></footer>
</section>

<section class="slide s5">
  <h2 class="heading">Talon Microsystems</h2>
  <p class="body">Lorem ipsum dolor sit amet, consectetur adipiscing elit, sed do eiusmod tempor incididunt ut labore et dolore magna aliqua. Ut enim ad minim veniam, quis nostrud exercitation ullamco laboris nisi ut aliquip ex ea commodo consequat. Duis aute irure dolor in reprehenderit in voluptate velit esse cillum dolore eu fugiat nulla pariatur. Excepteur sint occaecat cupidatat non proident, sunt in culpa qui officia deserunt mollit anim id est laborum.Lorem ipsum dolor sit amet, consectetur adipiscing elit, sed do eiusmod tempor incididunt ut labore et dolore magna aliqua. Ut enim ad minim veniam, quis nostrud exercitation ullamco laboris nisi ut aliquip ex ea commodo consequat. Duis aute irure dolor in reprehenderit in voluptate velit esse cillum dolore eu fugiat nulla pariatur. Excepteur sint occaecat cupidatat non proident, sunt in culpa qui officia deserunt mollit anim id est laborum.Lorem ipsum dolor sit amet, consectetur adipiscing elit, sed do eiusmod tempor incididunt ut labore et dolore magna aliqua. Ut enim ad minim veniam, quis nostrud exercitation ullamco laboris nisi ut aliquip ex ea commodo consequat.</p>
  <div class="orb orb1" role="img" aria-label="Circular photo of a glowing green chip on a circuit board"></div>
  <div class="orb orb2" role="img" aria-label="Circular photo of a machine tool working on a glowing wafer"></div>
  <footer class="footer"><span class="conf">TALON MICROSYSTEMS CONFIDENTIAL</span><div class="brand"><span class="dot"></span>Talon Microsystems</div><span class="page">PAGE | 05</span></footer>
</section>

<section class="slide s6">
  <div class="edge-top"></div>
  <div class="brand"><span class="dot"></span>Talon Microsystems</div>
  <div class="edge-bottom"></div>
</section>

</body>
</html>
```